Brightmill Data Works

Our company is about IT hardwares and IT solutions. IT hardware such as PC, RAMS, storage and servers. IT solutions such as project management, BA. We are also selling new technology too.

Target Market(s)

Consumer, Small to Medium Business, Corporate

Requirements
Must have
• The business card must have the following:
• Name:
• Title:
• Contact Number:
• Email address:
• Website:
• Color: Must match the logo color upgrade

```html
<!DOCTYPE html>
<html lang="en">
<head>
<meta charset="utf-8">
<title>Brightmill Data Works – Business Card</title>
<link href="https://fonts.googleapis.com/css2?family=Exo+2:wght@500;600;700&display=swap" rel="stylesheet">
<style>
  :root {
    --backdrop: #2b2b2b;
    --card-front: #f2f2f2;
    --card-back: #474747;
    --pattern-tone: #4e4944;
    --accent: #c8752f;
    --accent-light: #e39236;
    --ink: #4a4a4a;
    --white: #ffffff;
  }
  * { box-sizing: border-box; margin: 0; padding: 0; }
  html, body {
    width: 1200px; height: 960px; overflow: hidden;
    background: var(--backdrop);
    font-family: "Exo 2", sans-serif;
  }
  .canvas { position: relative; width: 1200px; height: 960px; }

  .card {
    position: absolute;
    width: 600px; height: 343px;
    box-shadow: 0 3px 8px rgba(0,0,0,0.45);
  }
  .card-front { left: 322px; top: 108px; background: var(--card-front); }
  .card-back { left: 320px; top: 493px; background: var(--card-back); }

  .guide-line {
    position: absolute; left: 48px; top: 0;
    width: 1.5px; height: 100%;
    background: var(--accent);
  }

  .brand-block {
    position: absolute; left: 332px; top: 24px; width: 250px;
    text-align: center;
  }
  .brand-mark {
    display: block; width: 30px; height: 30px;
    margin: 0 auto 14px;
    background: var(--accent);
  }
  .brand-name {
    font-weight: 700; font-size: 30px; line-height: 31px;
    letter-spacing: 0.5px; color: var(--ink);
  }

  .contact-row {
    position: absolute; left: 34px;
    display: flex; align-items: center;
  }
  .icon-diamond { width: 29px; height: 29px; flex: none; }
  .row-text {
    margin-left: 14px; font-weight: 600; font-size: 15px; color: var(--ink);
  }
  .person-name {
    font-weight: 500; font-size: 21px; color: var(--accent-light);
    line-height: 22px; margin-left: 12px;
  }
  .person-title {
    position: absolute; left: 75px; top: 180px;
    font-weight: 600; font-size: 15px; color: var(--ink);
  }
  .row-name { top: 151px; }
  .row-phone { top: 215px; }
  .row-email { top: 251px; }
  .row-web { top: 287px; }

  .back-pattern {
    position: absolute; inset: 0;
    background: linear-gradient(135deg, var(--pattern-tone), var(--card-back) 70%);
  }
  .back-name {
    position: absolute; left: 0; right: 0; top: 155px;
    text-align: center;
    font-weight: 700; font-size: 26px; letter-spacing: 1px;
    color: var(--accent-light);
  }
</style>
</head>
<body>
<main class="canvas">

  <section class="card card-front">
    <div class="guide-line"></div>

    <div class="brand-block">
      <span class="brand-mark"></span>
      <div class="brand-name">BRIGHTMILL<br>DATA WORKS</div>
    </div>

    <div class="contact-row row-name">
      <svg class="icon-diamond" viewBox="0 0 29 29" aria-hidden="true">
        <rect x="4.5" y="4.5" width="20" height="20" rx="2" transform="rotate(45 14.5 14.5)" fill="var(--accent)"/>
        <circle cx="14.5" cy="11.5" r="3" fill="var(--white)"/>
        <path d="M9 19.5c0-3 2.5-4.5 5.5-4.5s5.5 1.5 5.5 4.5z" fill="var(--white)"/>
      </svg>
      <span class="person-name">DANIEL HART</span>
    </div>
    <div class="person-title">CEO/FOUNDER</div>

    <div class="contact-row row-phone">
      <svg class="icon-diamond" viewBox="0 0 29 29" aria-hidden="true">
        <rect x="4.5" y="4.5" width="20" height="20" rx="2" transform="rotate(45 14.5 14.5)" fill="var(--accent)"/>
        <path d="M10.5 9.5l2-0.5 1.2 2.8-1.3 1c.7 1.5 1.8 2.6 3.3 3.3l1-1.3 2.8 1.2-.5 2c-5 .2-8.7-3.5-8.5-8.5z" fill="var(--white)"/>
      </svg>
      <span class="row-text">555 201 4836</span>
    </div>

    <div class="contact-row row-email">
      <svg class="icon-diamond" viewBox="0 0 29 29" aria-hidden="true">
        <rect x="4.5" y="4.5" width="20" height="20" rx="2" transform="rotate(45 14.5 14.5)" fill="var(--accent)"/>
        <rect x="9" y="10.5" width="11" height="8" fill="var(--white)"/>
        <path d="M9 10.5l5.5 4.5 5.5-4.5" fill="none" stroke="var(--accent)" stroke-width="1"/>
      </svg>
      <span class="row-text">daniel@brightmilldata.com</span>
    </div>

    <div class="contact-row row-web">
      <svg class="icon-diamond" viewBox="0 0 29 29" aria-hidden="true">
        <rect x="4.5" y="4.5" width="20" height="20" rx="2" transform="rotate(45 14.5 14.5)" fill="var(--accent)"/>
        <circle cx="14.5" cy="14.5" r="5.5" fill="none" stroke="var(--white)" stroke-width="1.3"/>
        <ellipse cx="14.5" cy="14.5" rx="2.3" ry="5.5" fill="none" stroke="var(--white)" stroke-width="1"/>
        <line x1="9" y1="14.5" x2="20" y2="14.5" stroke="var(--white)" stroke-width="1"/>
      </svg>
      <span class="row-text">www.brightmilldata.com</span>
    </div>
  </section>

  <section class="card card-back">
    <div class="back-pattern" role="img" aria-label="Faint repeating brand pattern in warm grey across the card back"></div>
    <div class="back-name">BRIGHTMILL DATA WORKS</div>
  </section>

</main>
</body>
</html>
```